Business Card Design

We need the business card for our new business based in St. Marys, we manufacture mainly bubble wraps. And we would like the design to use our company logo and also make it easy for people to understand right away we are bubble wrap manufacturer

Industry/Entity Type

Business

Contact Information for Business Card

Cushtane Pty Ltd, 14 Larkin Road Kellbrook NSW 2791, Tel: 02 9471 5826, Fax: 9471 5839, Dara Oyelaran, General Manager, Mobile :0438 217 564, dara.oyelaran@cushtane.com.au, Website: cushtane.com.au

```html
<!DOCTYPE html>
<html lang="en">
<head>
<meta charset="utf-8">
<title>Cushtane Business Card</title>
<link href="https://fonts.googleapis.com/css2?family=Arimo:wght@400;700&display=swap" rel="stylesheet">
<style>
  :root {
    --brand-red: #b0172a;
    --ink-grey: #555759;
    --paper: #ffffff;
    --backdrop: #e7e4df;
    --rule-light: rgba(255,255,255,0.75);
  }
  * { box-sizing: border-box; margin: 0; padding: 0; }
  html, body { width: 1200px; height: 848px; overflow: hidden; }
  body {
    background: var(--backdrop);
    font-family: "Arimo", Arial, sans-serif;
    display: flex; flex-direction: column; align-items: center; justify-content: center;
    gap: 40px;
  }
  .card {
    width: 660px; height: 377px; background: var(--paper);
    position: relative; overflow: hidden;
    box-shadow: 0 6px 18px rgba(0,0,0,0.18);
  }
  /* front */
  .front .top-band { position: absolute; left: 0; top: 0; width: 100%; height: 102px; }
  .front .red-band { position: absolute; left: 0; top: 102px; width: 100%; height: 172px; background: var(--brand-red); }
  .wordmark { display: flex; align-items: center; gap: 8px; }
  .wordmark .mark-square { width: 14px; height: 14px; background: var(--brand-red); }
  .wordmark .name { font-weight: 700; color: var(--ink-grey); letter-spacing: 1px; }
  .tagline { color: var(--ink-grey); text-transform: uppercase; letter-spacing: 3px; }
  .front .brand { position: absolute; left: 40px; top: 30px; }
  .front .brand .name { font-size: 34px; }
  .front .brand .tagline { font-size: 8.5px; margin-top: 5px; margin-left: 22px; }
  .person { position: absolute; left: 70px; top: 62px; color: var(--paper); }
  .person .full-name { font-size: 30px; line-height: 1; }
  .person .role { font-size: 13px; margin-top: 5px; margin-left: 4px; }
  .divider { position: absolute; left: 340px; top: 14px; width: 1px; height: 144px; background: var(--rule-light); }
  .contacts { position: absolute; left: 362px; top: 14px; width: 262px; list-style: none; color: var(--paper); }
  .contacts li {
    display: flex; align-items: center; gap: 10px; height: 28px;
    font-size: 13px; border-bottom: 1px solid var(--rule-light);
    white-space: nowrap;
  }
  .contacts svg { width: 12px; height: 12px; flex: none; fill: var(--paper); }
  .front .address {
    position: absolute; left: 0; right: 0; top: 274px; height: 103px;
    display: flex; align-items: center; justify-content: center;
    color: var(--ink-grey); font-size: 15px; padding-left: 80px;
    white-space: nowrap;
  }
  /* back */
  .back .red-band { position: absolute; left: 0; width: 100%; height: 96px; background: var(--brand-red); }
  .back .red-band.upper { top: 0; }
  .back .red-band.lower { bottom: 0; }
  .back .brand {
    position: absolute; left: 0; right: 0; top: 96px; height: 185px;
    display: flex; flex-direction: column; align-items: center; justify-content: center;
  }
  .back .brand .name { font-size: 56px; }
  .back .brand .tagline { font-size: 12px; letter-spacing: 5px; margin-top: 8px; }
  .back .wordmark .mark-square { width: 22px; height: 22px; }
</style>
</head>
<body>
  <section class="card front">
    <div class="top-band">
      <div class="brand">
        <div class="wordmark"><span class="mark-square"></span><span class="name">CUSHTANE</span></div>
        <div class="tagline">Protective Packaging Solutions</div>
      </div>
    </div>
    <div class="red-band">
      <div class="person">
        <div class="full-name">Dara Oyelaran</div>
        <div class="role">General Manager</div>
      </div>
      <div class="divider"></div>
      <ul class="contacts">
        <li><svg viewBox="0 0 12 12"><path d="M2.5 0.5l2 2.2-1 1.3c.7 1.6 2 2.9 3.5 3.6l1.3-1 2.2 2-1.2 1.9C5 10.3 1.7 7 0.5 1.7z"/></svg>02 9471 5826</li>
        <li><svg viewBox="0 0 12 12"><path d="M3 0h6v12H3zM4 1.5v8h4v-8z"/></svg>0438 217 564</li>
        <li><svg viewBox="0 0 12 12"><path d="M3 0h6v3H3zM0 4h12v5h-2v3H2V9H0zM3 7v4h6V7z"/></svg>9471 5839</li>
        <li><svg viewBox="0 0 12 12"><path d="M0 1h12v8H7v1.5h2V12H3v-1.5h2V9H0zM1 2v6h10V2z"/></svg>cushtane.com.au</li>
        <li><svg viewBox="0 0 12 12"><path d="M0 2h12v1L6 7 0 3zM0 4.2l6 4 6-4V10H0z"/></svg>dara.oyelaran@cushtane.com.au</li>
      </ul>
    </div>
    <div class="address">Cushtane Pty Ltd, 14 Larkin Road Kellbrook NSW 2791</div>
  </section>

  <section class="card back">
    <div class="red-band upper"></div>
    <div class="brand">
      <div class="wordmark"><span class="mark-square"></span><span class="name">CUSHTANE</span></div>
      <div class="tagline">Protective Packaging Solutions</div>
    </div>
    <div class="red-band lower"></div>
  </section>
</body>
</html>
```